Lumbra Ember Oven Kitchen (restaurant)

Restaurant with a cool vibe.
We need a refresh of existing site. Appealing to a hip crowd of 25 or older age bracket (mid price to high small town). Constant changes food and cocktail menu. A vibing atmosphere with jazz funk hip music.
Must be able to scale for any device… phone/mobile device super important.
Instagram: @Lumbra.Bexwell
Website: lumbrabexwell.example

Target Market(s)

25-55 age group

Number of Pages Required

1 page

Font styles to use
Sans Serif

Requirements
Must have
• Simple to navigate. Simplicity is the key to all sophistication.

Links/Buttons
Menu
Gift Cards
Reservations
Take Out
Contact Us
Should not have
• Please, nothing generic looking… no cookie cutter look. Originality

```html
<!DOCTYPE html>
<html lang="en">
<head>
<meta charset="utf-8">
<title>Lumbra Ember Oven Kitchen</title>
<link rel="stylesheet" href="https://fonts.googleapis.com/css2?family=Noto+Serif:wght@700&family=Roboto:wght@400;500;700;900&family=Poppins:wght@400;500&display=swap">
<style>
:root{
  --navy:#16415f;
  --navy-deep:#123a56;
  --yellow:#f7d21c;
  --gold:#f2c500;
  --ink:#111;
  --text:#333;
  --muted:#8a8a8a;
  --band:#efefef;
  --red:#e8211c;
  --white:#fff;
  --black:#000;
}
*{box-sizing:border-box;margin:0;padding:0}
html,body{width:1200px;height:4023px;overflow:hidden}
body{position:relative;background:var(--white);font-family:'Roboto',sans-serif;color:var(--text)}
.abs{position:absolute}
.serif{font-family:'Noto Serif',serif;font-weight:700;color:var(--ink)}
.topbar{left:0;top:0;width:1200px;height:10px;background:var(--navy)}
.brand{display:flex;flex-direction:column;align-items:center;line-height:1}
.brand .name{font-family:'Roboto',sans-serif;font-weight:900;font-size:42px;letter-spacing:2px;color:var(--black)}
.brand .tag{font-family:'Roboto',sans-serif;font-weight:900;font-size:14px;color:var(--black);margin-top:2px}
.socials{display:flex;gap:12px}
.socials span{width:34px;height:34px;border:1.5px solid #222;border-radius:50%;display:block;position:relative}
.socials span::after{content:"";position:absolute;left:13px;top:13px;width:6px;height:6px;border-radius:50%;background:#222}
.contact-item{display:flex;align-items:center;gap:12px}
.contact-item .lbl{font-weight:500;font-size:14px;color:#222}
.contact-item .val{font-size:15px;color:var(--muted);margin-top:4px}
.nav{top:104px;left:669px;display:flex;gap:0;font-family:'Noto Serif',serif;font-weight:700;font-size:15px;color:#222}
.nav a{color:#222;text-decoration:none;position:absolute;white-space:nowrap}
.hero-title{left:106px;top:352px;font-size:56px;line-height:47px;color:var(--white);font-family:'Noto Serif',serif;font-weight:700}
.hero-text{left:108px;top:463px;width:500px;font-family:'Poppins',sans-serif;font-size:16.5px;line-height:26px;color:var(--white)}
.btn{display:flex;align-items:center;justify-content:center;gap:8px;font-family:'Roboto',sans-serif;font-weight:700;font-size:15px;border-radius:24px;text-decoration:none}
.btn-yellow{background:var(--yellow);color:#111}
.btn-navy{background:var(--navy);color:var(--white)}
.btn-square{border-radius:2px;box-shadow:0 4px 8px rgba(0,0,0,.18)}
.arrow-ico{width:16px;height:16px;border-radius:50%;display:inline-flex;align-items:center;justify-content:center}
.slide-arrow{top:460px;width:20px;height:26px}
.about-photo{left:103px;top:886px;width:431px;height:470px;background:linear-gradient(135deg,#6b4a3a,#a8826a 40%,#e7ddd2 70%,#c7a46a)}
.h2{font-size:40px;line-height:1}
.para{font-size:15.5px;line-height:26px;color:var(--muted)}
.menu-band{left:0;top:1445px;width:1200px;height:521px;background:var(--band)}
.center-title{left:0;width:1200px;text-align:center}
.rule{width:56px;height:3px;background:var(--gold);left:572px}
.dish{width:260px;text-align:center}
.dish .plate{width:148px;height:148px;border-radius:50%;margin:0 auto;border:6px solid var(--yellow)}
.dish .plate.blue{border-color:var(--navy)}
.dish h3{font-family:'Noto Serif',serif;font-weight:700;font-size:14.5px;line-height:20px;color:#111;margin-top:18px}
.dish p{font-size:14px;line-height:21px;color:#333;margin-top:10px}
.dots span{display:inline-block;width:14px;height:14px;border-radius:50%;background:#111;margin:0 8px}
.dots span.on{background:var(--yellow)}
.gift{width:492px;height:336px;background:var(--white);box-shadow:0 0 6px rgba(0,0,0,.15);padding:9px}
.gift .inner{position:relative;width:100%;height:100%;border:2px solid var(--yellow);text-align:center;overflow:hidden}
.gift .corner{position:absolute;right:0;top:0}
.gift h3{font-family:'Noto Serif',serif;font-weight:700;font-size:21px;color:#111;margin-top:40px}
.gift .pct{font-family:'Roboto',sans-serif;font-weight:500;font-size:46px;color:var(--red);margin-top:8px;line-height:1}
.gift p{font-size:15.5px;line-height:26px;color:var(--muted);margin:16px auto 0;width:400px}
.gift .btn{width:158px;height:46px;margin:20px auto 0;font-size:15px}
.testi{left:0;top:2547px;width:1200px;height:453px;background:var(--navy-deep)}
.field{height:42px;border:1.5px solid #bdbdbd;background:var(--white);font-size:14.5px;color:#333;padding:12px 13px;display:flex;justify-content:space-between}
.footer-h{font-family:'Noto Serif',serif;font-size:16px;color:var(--yellow);text-decoration:underline;font-weight:400}
.footer-li{font-size:14.5px;color:var(--white);display:flex;align-items:center;gap:10px}
.footer-li::before{content:"»";font-size:15px}
.fc{display:flex;gap:16px;align-items:flex-start;color:var(--white)}
.fc .circ{width:34px;height:34px;border-radius:50%;background:var(--yellow);display:flex;align-items:center;justify-content:center;flex:none}
.fc b{font-size:12.5px;font-weight:700;display:block}
.fc span{font-size:15px;line-height:23px}
</style>
</head>
<body>

<div class="abs topbar"></div>

<!-- header -->
<header>
  <div class="abs brand" style="left:106px;top:28px">
    <span class="name">LUMBRA</span>
    <span class="tag">Ember Oven Kitchen</span>
  </div>
  <div class="abs socials" style="left:427px;top:41px" aria-label="Social links">
    <span></span><span></span><span></span><span></span>
  </div>
  <div class="abs contact-item" style="left:630px;top:36px">
    <svg width="36" height="36" viewBox="0 0 36 36" fill="none" stroke="#16415f" stroke-width="2"><circle cx="18" cy="18" r="16"/><path d="M12 11c1-1 2.5-1 3 0l1.5 3c.4.8 0 1.6-.6 2l-1 .8c1 2.2 2.6 3.8 4.8 4.8l.8-1c.5-.6 1.3-1 2-.6l3 1.5c1 .5 1 2 0 3-2 2-5 2-8-1s-6.5-6.5-6.5-8.5c0-1.5.4-2.8 1-4z"/></svg>
    <div><div class="lbl">Phone</div><div class="val">555-014-2290</div></div>
  </div>
  <div class="abs contact-item" style="left:808px;top:36px">
    <svg width="36" height="30" viewBox="0 0 36 30" fill="none" stroke="#16415f" stroke-width="2"><rect x="2" y="4" width="32" height="22"/><path d="M2 4l16 13 16-13M2 26l12-11M34 26l-12-11"/></svg>
    <div><div class="lbl">Email</div><div class="val">info@emberhouse.example</div></div>
  </div>
  <svg class="abs" style="left:1061px;top:49px" width="20" height="20" viewBox="0 0 20 20" fill="none" stroke="#16415f" stroke-width="2.6"><circle cx="8" cy="8" r="6"/><path d="M12.5 12.5l6 6"/></svg>
  <nav class="abs nav" style="left:0;top:104px;width:1200px">
    <a style="left:669px">HOME</a>
    <a style="left:762px">ABOUT ME</a>
    <a style="left:890px">MENU</a>
    <a style="left:983px">CONTACT US</a>
  </nav>
</header>

<!-- hero -->
<section>
  <svg class="abs" style="left:0;top:153px" width="1200" height="680" viewBox="0 0 1200 680">
    <defs>
      <linearGradient id="heroFill" x1="0" y1="0" x2="1" y2="1">
        <stop offset="0" stop-color="#3c4456"/>
        <stop offset=".35" stop-color="#7a4030"/>
        <stop offset=".7" stop-color="#5a2e24"/>
        <stop offset="1" stop-color="#2a2426"/>
      </linearGradient>
      <linearGradient id="heroShade" x1="0" y1="0" x2="1" y2="0">
        <stop offset="0" stop-color="#000" stop-opacity=".45"/>
        <stop offset=".6" stop-color="#000" stop-opacity=".1"/>
        <stop offset="1" stop-color="#000" stop-opacity="0"/>
      </linearGradient>
    </defs>
    <g role="img" aria-label="Photo of the brick restaurant building on a street corner">
      <path d="M0 0H1200V527Q600 745 0 527Z" fill="url(#heroFill)"/>
      <path d="M0 0H1200V527Q600 745 0 527Z" fill="url(#heroShade)"/>
    </g>
    <path d="M0 542Q600 776 1200 542" fill="none" stroke="#f2c500" stroke-width="1.5"/>
    <g fill="#f2c500">
      <circle cx="148" cy="589" r="6"/><circle cx="389" cy="642" r="6"/><circle cx="601" cy="659" r="6"/>
      <circle cx="719" cy="647" r="6"/><circle cx="842" cy="648" r="6"/><circle cx="1105" cy="577" r="6"/>
    </g>
  </svg>
  <svg class="abs slide-arrow" style="left:40px" viewBox="0 0 20 26"><path d="M15 3L5 13l10 10" fill="none" stroke="#fff" stroke-width="4"/></svg>
  <svg class="abs slide-arrow" style="left:1137px" viewBox="0 0 20 26"><path d="M5 3l10 10L5 23" fill="none" stroke="#fff" stroke-width="4"/></svg>
  <h1 class="abs hero-title">LUMBRA EMBER<br>OVEN KITCHEN</h1>
  <p class="abs hero-text">Lorem ipsum dolor sit amet, consectetur adipiscing elit, sed do eiusmod tempor incididunt ut labore et dolore magna aliqua.</p>
  <a class="abs btn btn-yellow" style="left:109px;top:539px;width:158px;height:47px">RESERVATIONS
    <span class="arrow-ico" style="background:#111"><svg width="10" height="10" viewBox="0 0 10 10"><path d="M1 5h7M5 2l3 3-3 3" stroke="#f7d21c" stroke-width="1.8" fill="none"/></svg></span></a>
  <a class="abs btn btn-navy" style="left:289px;top:539px;width:159px;height:47px;gap:14px">TAKE OUT
    <span class="arrow-ico" style="background:#fff"><svg width="10" height="10" viewBox="0 0 10 10"><path d="M1 5h7M5 2l3 3-3 3" stroke="#16415f" stroke-width="1.8" fill="none"/></svg></span></a>
</section>

<!-- about -->
<section>
  <div class="abs about-photo" role="img" aria-label="Photo of a smiling chef holding a plate of tacos"></div>
  <h2 class="abs serif h2" style="left:602px;top:905px">ABOUT US</h2>
  <p class="abs para" style="left:602px;top:979px;width:500px">Lorem ipsum dolor sit amet, consectetur adipiscing elit, sed do eiusmod tempor incididunt ut labore et dolore magna aliqua. Ut enim ad minim veniam, quis nostrud exercitation ullamco laboris nisi ut aliquip ex ea commodo consequat. Duis aute irure dolor in reprehenderit in voluptate velit esse cillum dolore eu fugiat nulla pariatur. Excepteur sint occaecat cupidatat non proident, sunt in culpa qui officia deserunt mollit laborum.</p>
  <p class="abs para" style="left:602px;top:1154px;width:500px">Lorem ipsum dolor sit amet, consectetur adipiscing elit, sed do eiusmod tempor incididunt ut labore et dolore magna aliqua. Ut enim ad minim veniam, quis nostrud exercitation ullamco laboris nisi ut aliquip ex ea commodo consequat. Duis aute irure dolor in reprehenderit in voluptate</p>
  <a class="abs btn btn-yellow" style="left:602px;top:1284px;width:159px;height:47px;gap:14px;box-shadow:0 3px 8px rgba(0,0,0,.15)">LEARN MORE
    <span class="arrow-ico" style="background:#111"><svg width="10" height="10" viewBox="0 0 10 10"><path d="M1 5h7M5 2l3 3-3 3" stroke="#f7d21c" stroke-width="1.8" fill="none"/></svg></span></a>
</section>

<!-- menu -->
<section>
  <div class="abs menu-band"></div>
  <h2 class="abs serif h2 center-title" style="top:1488px;font-size:36px">OUR MENU</h2>
  <div class="abs rule" style="top:1533px"></div>
  <div class="abs dish" style="left:65px;top:1595px">
    <div class="plate" role="img" aria-label="Photo of skewers on a plate" style="background:radial-gradient(circle,#c99060,#6a4a2c 70%)"></div>
    <h3>BUTTERNUT &amp;<br>SAUSAGE SKEWERS</h3>
    <p>Roasted butternut squash, grilled sausage, herbed ricotta, fresh arugula &amp; cherry tomato / 16</p>
  </div>
  <div class="abs dish" style="left:339px;top:1595px">
    <div class="plate blue" role="img" aria-label="Photo of flatbread in skillets" style="background:radial-gradient(circle,#b87a48,#3a3632 70%)"></div>
    <h3>JUNIPER FLATBREAD</h3>
    <p>Balsamic onion jam, smoked bacon, goat cheese, fresh arugula &amp; balsamic drizzle / 15</p>
  </div>
  <div class="abs dish" style="left:617px;top:1595px">
    <div class="plate" role="img" aria-label="Photo of wood fired green beans" style="background:radial-gradient(circle,#7a9a3a,#b4502c 70%)"></div>
    <h3>WOOD FIRED GREEN BEANS</h3>
    <p>Wood-oven green beans, fresh lemon, cherry tomato, shaved par-mesan, sriracha aioli / 12</p>
  </div>
  <div class="abs dish" style="left:886px;top:1595px">
    <div class="plate blue" role="img" aria-label="Photo of shrimp tacos" style="background:radial-gradient(circle,#d8c49a,#5a5a48 70%)"></div>
    <h3 style="margin-top:24px">PACIFIC SHRIMP TACOS</h3>
    <p>Wild pacific shrimp, spicy red pepper feta,fresh cucumber, radish, cherry tomato / x3 - 19</p>
  </div>
  <div class="abs dots center-title" style="top:1904px"><span></span><span class="on"></span><span></span></div>
</section>

<!-- gift cards -->
<section>
  <h2 class="abs serif h2 center-title" style="top:2047px;font-size:36px">GIFT CARDS</h2>
  <div class="abs rule" style="top:2090px"></div>
  <div class="abs gift" style="left:97px;top:2125px">
    <div class="inner">
      <svg class="corner" width="105" height="56" viewBox="0 0 105 56"><path d="M0 0H105V56Z" fill="#f7d21c"/><text x="90" y="18" font-family="Roboto,sans-serif" font-size="11" fill="#e8211c" text-anchor="end">50%</text><text x="96" y="32" font-family="Roboto,sans-serif" font-weight="700" font-size="12" fill="#111" text-anchor="end">Offer</text></svg>
      <h3>LOREM IPSUM DOLOR SIT</h3>
      <div class="pct">50%</div>
      <p>Lorem ipsum dolor sit amet, consectetur adipiscing elit, sed do eiusmod tempor ut labore et dolore magna nostrud exercitation ullamco laboris nisi ut aliquip.</p>
      <a class="btn btn-yellow btn-square">BUY GIFT CARDS</a>
    </div>
  </div>
  <div class="abs gift" style="left:611px;top:2125px">
    <div class="inner">
      <svg class="corner" width="105" height="56" viewBox="0 0 105 56"><path d="M0 0H105V56Z" fill="#f7d21c"/><text x="90" y="18" font-family="Roboto,sans-serif" font-size="11" fill="#e8211c" text-anchor="end">50%</text><text x="96" y="32" font-family="Roboto,sans-serif" font-weight="700" font-size="12" fill="#111" text-anchor="end">Offer</text></svg>
      <h3>LOREM IPSUM DOLOR SIT</h3>
      <div class="pct">50%</div>
      <p>Lorem ipsum dolor sit amet, consectetur adipiscing elit, sed do eiusmod tempor ut labore et dolore magna nostrud exercitation ullamco laboris nisi ut aliquip.</p>
      <a class="btn btn-yellow btn-square">BUY GIFT CARDS</a>
    </div>
  </div>
</section>

<!-- testimonials -->
<section>
  <div class="abs testi"></div>
  <div class="abs" role="img" aria-label="Photo of the colourful patio with a red umbrella" style="left:109px;top:2594px;width:268px;height:339px;background:linear-gradient(160deg,#d0402c,#3c7aa8 45%,#c85a2a 75%,#8a4a8a)"></div>
  <div class="abs" role="img" aria-label="Photo of a plated dish with greens" style="left:292px;top:2728px;width:227px;height:227px;background:linear-gradient(135deg,#5a4a3e,#c8b8a0 50%,#3a3a2e)"></div>
  <h2 class="abs" style="left:577px;top:2618px;font-family:'Noto Serif',serif;font-weight:700;font-size:36px;color:#fff">OUR TESTIMONIALS</h2>
  <svg class="abs" style="left:577px;top:2695px" width="62" height="52" viewBox="0 0 62 52" fill="#f7d21c"><path d="M0 30C0 12 10 2 24 0l2 6C17 9 13 15 13 22h12v30H0zM36 30C36 12 46 2 60 0l2 6C53 9 49 15 49 22h12v30H36z"/></svg>
  <p class="abs" style="left:577px;top:2771px;width:510px;font-size:15.5px;line-height:26px;color:#fff">Lorem ipsum dolor sit amet, consectetur adipiscing elit, sed do eiusmod tempor incididunt ut labore et dolore magna aliqua. Ut enim ad minim veniam, quis nostrud exercitation ullamco laboris nisi ut aliquip ex modo consequat. Duis aute irure dolor in reprehenderit in voluptate velit esse cillum dolore eu fugiat nulla pariatur.</p>
  <p class="abs" style="left:870px;top:2908px;width:200px;text-align:right;font-size:15.5px;font-weight:700;color:#fff">-Marla Venn</p>
</section>

<!-- contact form -->
<section>
  <h2 class="abs serif h2 center-title" style="top:3080px;font-size:36px">GET IN TOUCH</h2>
  <div class="abs field" style="left:255px;top:3164px;width:339px">First Name:</div>
  <div class="abs field" style="left:606px;top:3164px;width:339px">Last Name:</div>
  <div class="abs field" style="left:255px;top:3223px;width:339px">Phone Number:</div>
  <div class="abs field" style="left:606px;top:3223px;width:339px">Email:</div>
  <div class="abs field" style="left:255px;top:3283px;width:339px">Payment:<svg width="10" height="6" viewBox="0 0 10 6" style="margin-top:6px"><path d="M0 0h10L5 6z" fill="#16415f"/></svg></div>
  <div class="abs field" style="left:606px;top:3283px;width:339px">Address</div>
  <div class="abs field" style="left:255px;top:3344px;width:690px;height:73px">Comment:</div>
  <a class="abs btn btn-yellow btn-square" style="left:534px;top:3453px;width:133px;height:41px;gap:14px">SUBMIT
    <svg width="16" height="16" viewBox="0 0 16 16"><path d="M15 1L1 7l5 2 1 6 3-4 4 3z" fill="#111"/></svg></a>
</section>

<!-- footer -->
<footer>
  <svg class="abs" style="left:0;top:3540px" width="1200" height="483" viewBox="0 0 1200 483">
    <path d="M0 171Q600 -95 1200 171V483H0Z" fill="#000"/>
    <path d="M0 148Q600 -78 1200 148" fill="none" stroke="#f2c500" stroke-width="1.5"/>
    <g fill="#f2c500"><circle cx="16" cy="142" r="6"/><circle cx="394" cy="49" r="6"/><circle cx="605" cy="35" r="6"/><circle cx="847" cy="54" r="6"/><circle cx="1109" cy="116" r="6"/></g>
  </svg>
  <div class="abs brand" style="left:112px;top:3704px">
    <span class="name" style="color:#fff;font-size:34px">LUMBRA</span>
    <span class="tag" style="color:#fff;font-size:11px;font-weight:400">Ember Oven Kitchen</span>
  </div>
  <div class="abs footer-h" style="left:112px;top:3773px">Takeout &amp; Kitchen Hours</div>
  <div class="abs footer-li" style="left:112px;top:3813px">Thursday to Sunday12:00pm - 8:00pm</div>
  <div class="abs footer-h" style="left:112px;top:3856px">Outdoor Dining Hours</div>
  <div class="abs footer-li" style="left:112px;top:3895px">Thursday to Sunday 12:00pm - 9:00pm</div>

  <div class="abs footer-h" style="left:450px;top:3704px">Canada Day Hours!</div>
  <div class="abs footer-li" style="left:450px;top:3743px">Thursday, July 1st&nbsp; - &nbsp;Open</div>
  <div class="abs footer-li" style="left:450px;top:3782px">Friday, July 2nd&nbsp; - &nbsp;Open</div>
  <div class="abs footer-li" style="left:450px;top:3820px">Saturday, July 3rd&nbsp; - &nbsp;Open</div>
  <div class="abs footer-li" style="left:450px;top:3859px">Sunday, July 4th&nbsp; - &nbsp;Closed</div>

  <div class="abs footer-h" style="left:705px;top:3704px">Otherlinks</div>
  <div class="abs footer-li" style="left:705px;top:3743px">Home</div>
  <div class="abs footer-li" style="left:705px;top:3782px">About Us</div>
  <div class="abs footer-li" style="left:705px;top:3820px">Menu</div>
  <div class="abs footer-li" style="left:705px;top:3859px">Contact Us</div>

  <div class="abs footer-h" style="left:862px;top:3704px;font-weight:700">Contact Us</div>
  <div class="abs fc" style="left:862px;top:3745px">
    <span class="circ"><svg width="16" height="16" viewBox="0 0 16 16"><path d="M3 1c1-1 2-1 2.5 0L7 4c.3.6 0 1.3-.5 1.7l-.8.6c.9 1.8 2.2 3.2 4 4l.6-.8c.4-.5 1.1-.8 1.7-.5l3 1.5c1 .5 1 1.5 0 2.5-2 2-5 1-8-2S1 4 3 1z" fill="#111"/></svg></span>
    <div><b>Phone Number :</b><span>555-014-2290</span></div>
  </div>
  <div class="abs fc" style="left:862px;top:3803px">
    <span class="circ"><svg width="16" height="12" viewBox="0 0 16 12" fill="none" stroke="#111" stroke-width="1.6"><rect x="1" y="1" width="14" height="10"/><path d="M1 1l7 6 7-6"/></svg></span>
    <div><b>Email:</b><span>hello@lumbrabexwell.example</span></div>
  </div>
  <div class="abs fc" style="left:862px;top:3866px">
    <span class="circ"><svg width="14" height="18" viewBox="0 0 14 18"><path d="M7 0a7 7 0 0 1 7 7c0 5-7 11-7 11S0 12 0 7a7 7 0 0 1 7-7z" fill="#111"/><circle cx="7" cy="7" r="2.5" fill="#f7d21c"/></svg></span>
    <div><b>Address :</b><span>18 Harlow Street<br>Bexwell, ON</span></div>
  </div>

  <div class="abs" style="left:112px;top:3969px;width:976px;height:1px;background:#444"></div>
  <div class="abs" style="left:112px;top:3992px;display:flex;gap:20px" aria-label="Social links">
    <span style="width:8px;height:8px;background:#fff;display:block"></span>
    <span style="width:8px;height:8px;background:#fff;display:block"></span>
    <span style="width:8px;height:8px;background:#fff;display:block"></span>
    <span style="width:8px;height:8px;background:#fff;display:block"></span>
  </div>
  <p class="abs" style="left:0;top:3988px;width:1200px;text-align:center;font-size:14px;color:#fff">© 2021 Copyrights I Lumbra Ember Oven Kitchen | All Rights Reserved</p>
</footer>

</body>
</html>
```